Animal Horse & Bedding Company Needs a Website Coded & Designed

We need a website for a new animal bedding and feed company that is visually grabbing and vibrant. We would like to see a website that displays trust, quality and confidence. Needs to be responsive and mobile friendly for all browsers and coded for both Android & IOS. SEO is also important.

Joomla or Wordpress – must be both desktop and mobile friendly with fast page load speed. Need the ability to edit ourselves in Wordpress or Joomla.

Full details attached below with some layout and content ideas.

Coding

Coded - Design and coding required

Number of Pages Required

5+ page

Font styles to use
Sans Serif

Requirements
Must have
• Needs to be responsive and mobile friendly for all browsers and coded for both Android & IOS. SEO is also important.

Wordpress – must be both desktop and mobile friendly with fast page load speed. Need the ability to edit ourselves in Wordpress.

Logo Colours:
Dark Brown
CMYK: 50 / 70 / 80 / 70
Pantone: 4625C

Orange
CMYK: 0 / 50 / 100 / 0
Pantone: 144C
Nice to have
• Use picture of building attached and super impose logo on building.

```html
<!DOCTYPE html>
<html lang="en">
<head>
<meta charset="utf-8">
<title>Golden Bale – Bedding &amp; Feed</title>
<link href="https://fonts.googleapis.com/css2?family=Oswald:wght@300;400&family=Poppins:wght@400;500;600&display=swap" rel="stylesheet">
<style>
:root{
  --brown:#4a2a1a;
  --brown-dark:#3a2114;
  --orange:#f7941d;
  --white:#ffffff;
  --ink:#333333;
  --muted:#8a8a8a;
  --canvas:#f1f1f1;
}
*{box-sizing:border-box;margin:0;padding:0}
html,body{width:1200px;height:2866px;overflow:hidden}
body{background:var(--canvas);font-family:'Poppins',sans-serif;color:var(--ink)}
.page{position:absolute;left:100px;top:0;width:1000px;height:2866px;background:var(--white);box-shadow:0 0 24px rgba(0,0,0,.12)}
.display{font-family:'Oswald',sans-serif;font-weight:300;text-transform:uppercase;letter-spacing:.5px}
.btn{display:inline-block;background:var(--orange);color:var(--white);font-family:'Oswald',sans-serif;font-weight:300;text-transform:uppercase;letter-spacing:1px;text-align:center;border-radius:2px}

/* header */
.topbar{position:relative;height:84px;background:linear-gradient(180deg,#4a2c1c,#3a2114)}
.contact{position:absolute;left:64px;top:20px;font-size:11px;color:var(--white);line-height:22px}
.contact svg{vertical-align:middle;margin-right:12px}
.brand{position:absolute;left:50%;top:26px;transform:translateX(-50%);font-family:'Oswald',sans-serif;font-weight:400;font-size:26px;color:var(--white);letter-spacing:1px;display:flex;align-items:center;gap:10px}
.brand i{display:block;width:12px;height:12px;background:var(--orange)}
.search{position:absolute;left:723px;top:30px;width:224px;height:26px;background:var(--white);border-radius:2px;font-size:10px;color:#bbb;padding:6px 12px}
.search svg{position:absolute;right:10px;top:8px}
.nav{height:30px;background:var(--orange);display:flex;justify-content:center;gap:50px;align-items:center;font-size:13px;color:var(--white)}

/* hero */
.hero{position:relative;height:490px;background:linear-gradient(100deg,#e3a548 0%,#f0bf5c 30%,#d8c27a 55%,#9fbccf 75%,#7fa4c2 100%)}
.hero-horse{position:absolute;left:520px;top:30px;width:470px;height:420px;border-radius:40% 30% 10% 10%;background:radial-gradient(ellipse at 50% 45%,#b3501c,#8a3c14 60%,rgba(138,60,20,0) 72%)}
.hero-grass{position:absolute;left:0;bottom:0;width:100%;height:110px;background:linear-gradient(180deg,rgba(140,160,40,0),#a5b83a 60%,#c6d24e)}
.hero-text{position:absolute;left:80px;top:118px;color:var(--white)}
.hero-text .welcome{font-size:30px}
.hero-text h1{font-family:'Oswald',sans-serif;font-weight:400;font-size:80px;line-height:88px;text-transform:uppercase}
.hero-text .sub{font-size:42px;letter-spacing:2px;margin-top:4px}
.hero-text .btn{width:110px;height:27px;line-height:27px;font-size:12px;margin-top:16px}

/* about */
.about{position:relative;height:423px}
.about-mark{position:absolute;left:127px;top:70px;width:215px;height:260px;display:flex;flex-direction:column;align-items:center;justify-content:center;gap:18px}
.about-mark i{display:block;width:150px;height:150px;border-radius:50%;background:#efe4da}
.about-mark span{font-family:'Oswald',sans-serif;font-weight:400;font-size:26px;color:var(--brown)}
.about-copy{position:absolute;left:479px;top:82px;width:390px}
.about-copy h2{font-size:40px;color:var(--brown);font-weight:400}
.about-copy p{font-size:11.5px;line-height:17.5px;margin-top:24px;color:var(--ink)}
.about-copy .btn{width:110px;height:27px;line-height:27px;font-size:12px;margin-top:30px}

/* benefit bands */
.band{position:relative;height:324px;overflow:hidden}
.band.bedding{background:linear-gradient(180deg,#53574d 0%,#4c5a3e 55%,#5a8c2a 80%,#4f8a22 100%)}
.band.feed{height:323px;background:linear-gradient(180deg,#2f3a2a 0%,#5b4a33 40%,#4d7a22 80%,#3f6a1c 100%)}
.band .photo{position:absolute}
.bedding .photo{left:480px;top:0;width:520px;height:324px;background:radial-gradient(ellipse at 55% 55%,#7a3d1f,rgba(122,61,31,0) 60%)}
.feed .photo{left:0;top:0;width:560px;height:323px;background:radial-gradient(ellipse at 40% 50%,#6b3a22,rgba(107,58,34,0) 62%)}
.benefit-box{position:absolute;top:43px;width:401px;height:238px;border:2px solid var(--orange);background:rgba(25,20,15,.55);padding:34px 40px 0;color:var(--white)}
.bedding .benefit-box{left:45px}
.feed .benefit-box{left:553px}
.benefit-box h2{font-size:36px;font-weight:300;line-height:40px}
.bullets{display:flex;gap:18px;margin-top:8px;font-size:8.5px;line-height:12.5px;letter-spacing:.3px}
.bullets ul{list-style:none}
.bullets li::before{content:"• "}
.benefit-box .btn{position:absolute;left:40px;bottom:24px;width:110px;height:27px;line-height:27px;font-size:12px}

/* products */
.products{position:relative;height:382px}
.section-title{font-size:38px;color:var(--brown);font-weight:400}
.underline{display:block;width:65px;height:3px;background:var(--brown);margin-top:6px}
.products .heading{position:absolute;left:81px;top:48px}
.arrow-text{position:absolute;top:194px;font-size:22px;color:var(--brown);font-family:'Oswald',sans-serif;font-weight:300}
.card{position:absolute;top:143px;width:264px;height:143px;background:var(--white);box-shadow:0 1px 6px rgba(0,0,0,.14)}
.card .thumb{position:absolute;left:16px;top:20px;width:103px;height:100px}
.card h3{position:absolute;left:146px;top:42px;font-size:10px;line-height:13px;font-weight:600;color:var(--ink)}
.card .btn{position:absolute;left:146px;top:90px;width:84px;height:22px;line-height:22px;font-size:8px}

/* testimonial */
.testimonial{position:relative;height:520px}
.testimonial .heading{position:absolute;left:0;top:50px;width:100%;text-align:center}
.testimonial .underline{margin:6px auto 0}
.t-card{position:absolute;top:148px;width:211px;height:237px;background:var(--white);box-shadow:0 1px 8px rgba(0,0,0,.14);text-align:center;padding-top:26px}
.t-card .avatar{width:38px;height:38px;border-radius:50%;background:#c9ccd1;margin:0 auto}
.t-card h4{font-size:12px;font-weight:600;margin-top:10px}
.t-card .stars{color:var(--orange);font-size:11px;letter-spacing:3px;margin-top:2px}
.t-card p{font-size:9.5px;line-height:15px;color:var(--muted);margin:14px 24px 0}
.circle-arrow{position:absolute;top:252px}

/* newsletter */
.newsletter{position:absolute;left:114px;top:2525px;width:771px;height:75px;background:var(--orange);z-index:2;display:flex;align-items:center;padding:0 28px}
.newsletter .label{font-size:19px;color:var(--brown);font-weight:400;width:236px}
.newsletter .field{width:340px;height:30px;background:var(--white);font-size:11px;color:#aaa;padding:8px 14px}
.newsletter .submit{width:136px;height:30px;margin-left:12px;background:var(--brown);color:var(--white);font-family:'Oswald',sans-serif;font-weight:300;font-size:15px;text-align:center;line-height:30px;text-transform:uppercase}

/* footer */
.footer{position:absolute;left:0;top:2576px;width:1000px;height:290px;background:var(--brown);color:var(--white)}
.footer .f-brand{position:absolute;left:115px;top:84px;width:200px;font-family:'Oswald',sans-serif;font-size:24px;display:flex;align-items:center;gap:10px}
.footer .f-brand i{display:block;width:10px;height:10px;background:var(--orange)}
.footer .about-line{position:absolute;left:134px;top:145px;width:190px;font-size:11px;line-height:16px;letter-spacing:.5px}
.f-col{position:absolute;top:72px}
.f-col h5{font-size:16px;font-weight:500;border-bottom:1px solid var(--white);display:inline-block;padding-bottom:2px}
.f-col ul{list-style:none;font-size:11px;margin-top:14px}
.col-touch{left:385px}.col-touch li{margin-bottom:22px}
.col-links{left:563px}.col-links li{line-height:18px;font-weight:500}
.col-connect{left:739px}
.col-connect .tag{font-size:6.5px;margin-top:8px}
.col-connect li{display:flex;align-items:center;gap:16px;line-height:24px;font-size:10px}
.col-connect li i{display:block;width:10px;height:10px;background:var(--white);border-radius:50%}
.footer .rule{position:absolute;left:114px;top:262px;width:771px;height:1px;background:rgba(255,255,255,.5)}
.footer .copy{position:absolute;left:0;top:270px;width:100%;text-align:center;font-size:10px}
</style>
</head>
<body>
<div class="page">
  <header>
    <div class="topbar">
      <div class="contact">
        <div><svg width="12" height="12" viewBox="0 0 24 24"><path fill="#f7941d" d="M6.6 10.8c1.4 2.8 3.8 5.1 6.6 6.6l2.2-2.2c.3-.3.7-.4 1-.2 1.1.4 2.3.6 3.6.6.6 0 1 .4 1 1V20c0 .6-.4 1-1 1C10.6 21 3 13.4 3 4c0-.6.4-1 1-1h3.5c.6 0 1 .4 1 1 0 1.3.2 2.5.6 3.6.1.3 0 .7-.2 1z"/></svg>0800-555-0142</div>
        <div><svg width="12" height="10" viewBox="0 0 24 18"><rect width="24" height="18" fill="#f7941d"/><path d="M0 0l12 9L24 0" stroke="#3a2114" stroke-width="2" fill="none"/></svg>hello@goldenbale.com</div>
      </div>
      <div class="brand"><i></i>GOLDEN BALE</div>
      <div class="search">Search<svg width="10" height="10" viewBox="0 0 24 24"><circle cx="10" cy="10" r="7" stroke="#f7941d" stroke-width="3" fill="none"/><path d="M15 15l7 7" stroke="#f7941d" stroke-width="3"/></svg></div>
    </div>
    <nav class="nav"><span>Home</span><span>About</span><span>Feed</span><span>Bedding</span><span>Contact Us</span><span>Requets Quote</span></nav>
  </header>

  <section class="hero" role="img" aria-label="Chestnut horse standing in a golden sunlit meadow with tall grass">
    <div class="hero-horse"></div>
    <div class="hero-grass"></div>
    <div class="hero-text display">
      <div class="welcome">Wellcome</div>
      <h1>Golden Bale</h1>
      <div class="sub">Bedding &amp; Feed</div>
      <span class="btn">Shop Now</span>
    </div>
  </section>

  <section class="about">
    <div class="about-mark"><i></i><span>Golden Bale</span></div>
    <div class="about-copy">
      <h2 class="display">About Us</h2>
      <p>Looking for the best bedding and feed for your horse, livestock or household pet look no further. We use premium locally sourced straw and hay in all of our products and are committed in providing quality products and service.<br>Your animal deserves the very best in health and comfort to keep them healthy, strong and happy. Our products are designed for horses, livestock (goats, cattle and sheep), small caged animals (rabbits, guinea pigs and more).</p>
      <span class="btn">Learn More</span>
    </div>
  </section>

  <section class="band bedding">
    <div class="photo" role="img" aria-label="Young foal on green grass eating from a black feed bucket"></div>
    <div class="benefit-box">
      <h2 class="display">Bedding Benefit</h2>
      <div class="bullets">
        <ul><li>100% Natural Chopped<br>&nbsp;&nbsp;Straw</li><li>Low Dust</li><li>Chemical &amp; Additive Free</li><li>Clean &amp; Highly Absorbent</li><li>Cheaper than Wood<br>&nbsp;&nbsp;Shavings</li></ul>
        <ul><li>Economic – less used and less wasted</li><li>Environmentally Friendly – Recyclable<br>&nbsp;&nbsp;&amp; Compostable</li></ul>
      </div>
      <span class="btn">Shop Now</span>
    </div>
  </section>

  <section class="products">
    <div class="heading"><h2 class="section-title display">Our Products</h2><span class="underline"></span></div>
    <span class="arrow-text" style="left:30px">&lt;&lt;</span>
    <div class="card" style="left:81px"><div class="thumb" role="img" aria-label="Chestnut horse portrait" style="background:linear-gradient(135deg,#6b8a3a,#9a4a1e)"></div><h3>Best Bedding<br>For Your Horse</h3><span class="btn">Requets Quote</span></div>
    <div class="card" style="left:367px"><div class="thumb" role="img" aria-label="Woolly sheep close up" style="background:linear-gradient(135deg,#cfe0ef,#b08c5a)"></div><h3>Best Bedding<br>For Your Horse</h3><span class="btn">Requets Quote</span></div>
    <div class="card" style="left:653px"><div class="thumb" role="img" aria-label="White rabbit sitting in grass" style="background:linear-gradient(135deg,#4e6f2a,#e8e8e4)"></div><h3>Best Feed For<br>Your Horse</h3><span class="btn">Requets Quote</span></div>
    <span class="arrow-text" style="left:948px">&gt;&gt;</span>
  </section>

  <section class="band feed">
    <div class="photo" role="img" aria-label="Brown and white cattle grazing on a green pasture"></div>
    <div class="benefit-box">
      <h2 class="display">Feed Benefit</h2>
      <div class="bullets">
        <ul><li>100% Natural</li><li>Chemical &amp; Additive Free</li><li>Available in Pellets or Cubes</li><li>High Protein Content</li><li>Eliminate Waste in Feeding</li><li>Clean – Eliminates Dust From<br>&nbsp;&nbsp;Feeding Baled Hay</li></ul>
        <ul><li>Cost Effective</li><li>Convenient</li><li>Less wasted feed</li></ul>
      </div>
      <span class="btn">Shop Now</span>
    </div>
  </section>

  <section class="testimonial">
    <div class="heading"><h2 class="section-title display">Testimonial</h2><span class="underline"></span></div>
    <svg class="circle-arrow" style="left:60px" width="24" height="24" viewBox="0 0 24 24"><circle cx="12" cy="12" r="12" fill="#555"/><path d="M14 7l-5 5 5 5" stroke="#fff" stroke-width="2.4" fill="none"/></svg>
    <div class="t-card" style="left:141px"><div class="avatar"></div><h4>Martin Ashby</h4><div class="stars">★★★★★</div><p>Lorem ipsum dolor sit amet, consectetur adipiscing elit ut aliquam, purus sit amet luctus venenatis, lectus magna purus sit amet luctus venenatis.</p></div>
    <div class="t-card" style="left:394px"><div class="avatar"></div><h4>Martin Ashby</h4><div class="stars">★★★★★</div><p>Lorem ipsum dolor sit amet, consectetur adipiscing elit ut aliquam, purus sit amet luctus venenatis, lectus magna purus sit amet luctus venenatis.</p></div>
    <div class="t-card" style="left:648px"><div class="avatar"></div><h4>Martin Ashby</h4><div class="stars">★★★★★</div><p>Lorem ipsum dolor sit amet, consectetur adipiscing elit ut aliquam, purus sit amet luctus venenatis, lectus magna purus sit amet luctus venenatis.</p></div>
    <svg class="circle-arrow" style="left:905px" width="24" height="24" viewBox="0 0 24 24"><circle cx="12" cy="12" r="12" fill="#555"/><path d="M10 7l5 5-5 5" stroke="#fff" stroke-width="2.4" fill="none"/></svg>
  </section>

  <div class="newsletter">
    <div class="label display">Subscribe for Newsletter</div>
    <div class="field">Your Email Address</div>
    <div class="submit">Subscribe</div>
  </div>

  <footer class="footer">
    <div class="f-brand"><i></i>GOLDEN BALE</div>
    <p class="about-line">Golden Bale offers supply and delivery of fresh bedding as well as removal of waste bedding.</p>
    <div class="f-col col-touch"><h5>Get in touch</h5><ul><li>0811-555-0101</li><li>022-5550177</li><li>0811-555-0199</li></ul></div>
    <div class="f-col col-links"><h5>Useful Links</h5><ul><li>Home</li><li>About</li><li>Feed</li><li>Bedding</li><li>Contact Us</li><li>Request Quote</li></ul></div>
    <div class="f-col col-connect"><h5>Connect</h5><div class="tag">Be apart of Golden Bale family</div><ul><li><i></i>Photos</li><li><i></i>Community</li><li><i></i>Updates</li><li><i></i>Videos</li></ul></div>
    <div class="rule"></div>
    <div class="copy">© Copyright 2020 Golden Bale. All Rights Reserved.</div>
  </footer>
</div>
</body>
</html>
```